Swing Dance Themed Cleaning Company Website

We need a website designed for a cleaning company based in Portland, Oregon called Foxtrot Lane. We clean homes and commercial buildings, inside and out.

needs to be vintage and like the velvet tambour. Speakeasy 1920s feel.
needs to be classy.

Check out foxtrotlane.com We are not happy with the site currently.

please look at house scout site for more content https://www.housescoutpro.com/rated.FoxtrotLaneCleaning.48217705.html

Check out my videos on my ClipHaven channel Foxtrot Lane

Target Market(s)

middle class and home owner

Industry/Entity Type

Cleaning Service

Number of Pages Required

3 page

Font styles to use
Other font styles liked:
• jazzrag

Colors

Designer to choose colors to be used in the design.

Requirements
Must have
• must be good on pc and mobile

```html
<!DOCTYPE html>
<html lang="en">
<head>
<meta charset="utf-8">
<title>Foxtrot Lane — Cleaning Services Portland</title>
<link rel="stylesheet" href="https://fonts.googleapis.com/css2?family=Poiret+One&family=Oswald:wght@400;500;600&family=Open+Sans:wght@400;600;700&display=swap">
<style>
:root{
  --yellow:#fff200;
  --yellow-deep:#f2e500;
  --beige:#e9e6d8;
  --ink:#232323;
  --charcoal:#2b2b2b;
  --white:#ffffff;
  --muted:#555555;
  --field:#f1f1f1;
}
*{box-sizing:border-box;margin:0;padding:0}
html,body{width:1200px;height:3719px;overflow:hidden}
body{position:relative;background:var(--beige);font-family:"Open Sans",sans-serif;color:var(--ink)}
.abs{position:absolute}
.backdrop{position:absolute;left:0;top:0;width:1200px;height:3719px}

/* navigation */
.topnav{left:0;top:0;width:1200px;height:80px;background:var(--yellow-deep);box-shadow:0 2px 6px rgba(0,0,0,.15)}
.topnav a{position:absolute;top:30px;font:600 14px "Oswald",sans-serif;color:var(--ink);text-decoration:none;letter-spacing:.5px}
.brand-box{left:478px;top:0;width:244px;height:82px;background:var(--ink);text-align:center;padding-top:12px}
.brand-name{display:flex;align-items:center;justify-content:center;gap:10px;font:600 28px/1 "Oswald",sans-serif;color:var(--yellow);text-transform:uppercase}
.brand-name span.mark{width:20px;height:20px;background:var(--yellow);display:inline-block}
.brand-tag{margin-top:10px;font:400 9px "Open Sans",sans-serif;color:var(--yellow);letter-spacing:1px;text-transform:uppercase}

/* section titles */
.section-title{left:0;width:1200px;display:flex;align-items:center;justify-content:center;gap:22px}
.section-title .rule{width:150px;height:2px;background:var(--ink)}
.section-title .diamond{width:14px;height:14px;background:var(--ink);transform:rotate(45deg)}
.section-title h2{
  font:400 80px/1 "Poiret One",sans-serif;color:var(--yellow);letter-spacing:2px;text-transform:uppercase;
  text-shadow:2px 0 0 var(--ink),-2px 0 0 var(--ink),0 2px 0 var(--ink),0 -2px 0 var(--ink),
              1.5px 1.5px 0 var(--ink),-1.5px -1.5px 0 var(--ink),1.5px -1.5px 0 var(--ink),-1.5px 1.5px 0 var(--ink);
}
.section-title.dark .rule,.section-title.dark .diamond{background:var(--yellow)}
.section-title.dark h2{text-shadow:none;color:var(--yellow);font-weight:400}
.section-title.main h2{font-size:82px}

.intro{left:300px;width:600px;top:258px;text-align:center;font-size:17px;line-height:26px}

/* slider */
.slider-media{left:228px;top:367px;width:744px;height:352px;background:linear-gradient(135deg,#d8cfc6,#c9b9ab 55%,#7fbf9a)}
.slider-caption{left:300px;width:600px;top:736px;text-align:center;color:var(--white);font-size:14px;line-height:22px}
.slider-dots{left:577px;top:822px;display:flex;gap:8px}
.slider-dots i{width:12px;height:12px;background:var(--white);display:block}
.slider-dots i.on{background:var(--yellow)}
.quote-btn{left:410px;top:872px;width:380px;text-align:center;font:600 16px "Oswald",sans-serif;color:var(--ink);line-height:42px}

/* about */
.about-heading{left:0;width:1200px;top:1096px;text-align:center;font:600 28px "Oswald",sans-serif}
.about-text{left:250px;width:700px;top:1150px;text-align:center;font-size:14px;line-height:26px;color:var(--muted)}
.btn{position:absolute;height:40px;border:2px solid var(--ink);background:var(--white);font:600 12px/36px "Open Sans",sans-serif;text-align:center;color:var(--ink)}
.about-link{left:0;width:1200px;top:1308px;text-align:center;font:600 26px "Oswald",sans-serif;text-decoration:underline}

/* services */
.service h3{position:absolute;font:600 22px "Oswald",sans-serif;text-transform:uppercase}
.service-photo{position:absolute;width:161px;height:186px;clip-path:polygon(50% 0,100% 25%,100% 75%,50% 100%,0 75%,0 25%)}
.service ul{position:absolute;list-style:none;font-size:13px;line-height:24px}
.service li::before{content:"•";margin-right:7px}
.service li.cont{padding-left:13px}
.service li.cont::before{content:none}

/* blog */
.blog-sub{left:0;width:1200px;top:2505px;text-align:center;font:600 28px "Oswald",sans-serif}
.post-card{position:absolute;width:153px;height:181px;background:var(--white);box-shadow:0 2px 6px rgba(0,0,0,.2)}
.post-card .photo{width:153px;height:116px}
.post-card .cam{position:absolute;left:62px;top:104px;width:28px;height:28px;border-radius:50%;background:var(--yellow)}
.post-card .label{position:absolute;left:0;width:153px;top:146px;text-align:center;font:600 12px "Oswald",sans-serif;text-transform:uppercase}
.post-title{position:absolute;width:270px;font:600 18px/26px "Oswald",sans-serif}
.post-meta{position:absolute;width:270px;font-size:11px;color:var(--muted);border-top:1px solid #999;border-bottom:1px solid #999;padding:6px 0}
.post-date{position:absolute;width:34px;height:46px;background:var(--ink);color:var(--white);text-align:center;font:700 13px/18px "Open Sans",sans-serif;padding-top:4px}
.post-date small{display:block;font-size:10px;font-weight:400}
.post-excerpt{position:absolute;width:226px;font-size:11px;line-height:17px;color:var(--muted)}
.post-more{position:absolute;font:700 11px "Open Sans",sans-serif;text-decoration:underline}

/* contact */
.contact-lead{left:250px;width:700px;top:3170px;text-align:center;font:500 28px/40px "Oswald",sans-serif;color:var(--white)}
.field{position:absolute;left:174px;width:411px;background:var(--field);font-size:11px;color:#777;padding:12px 10px}
.submit{left:174px;top:3627px;width:116px;height:43px;background:var(--yellow);font:600 14px/43px "Oswald",sans-serif;text-align:center;color:var(--ink)}
.info-rule{position:absolute;left:612px;width:414px;height:1px;background:#555}
.info-row{position:absolute;left:612px;display:flex;align-items:center;gap:14px;color:var(--white);font:600 13px "Open Sans",sans-serif}
.info-row svg{width:22px;height:18px}
.social{position:absolute;top:3483px;width:74px;height:74px;border-radius:50%;background:var(--yellow)}
.copyright{left:612px;top:3588px;font-size:11px;color:var(--white)}
</style>
</head>
<body>

<svg class="backdrop" viewBox="0 0 1200 3719" aria-hidden="true">
  <rect x="0" y="0" width="1200" height="3719" fill="var(--beige)"/>
  <polygon points="0,0 1200,0 1200,525 600,640 0,525" fill="var(--yellow)"/>
  <polygon points="0,1326 600,1450 1200,1326 1200,2132 600,2330 0,2132" fill="var(--yellow)"/>
  <polygon points="0,2851 600,2975 1200,2851 1200,3719 0,3719" fill="var(--charcoal)"/>
  <polygon points="161,335 1039,335 1039,880 600,905 161,880" fill="var(--charcoal)"/>
  <polygon points="410,872 790,872 740,917 460,917" fill="var(--yellow)"/>
</svg>

<header class="abs topnav">
  <a style="left:162px" href="#">HOME</a>
  <a style="left:243px" href="#">CONTACT US</a>
  <a style="left:368px" href="#">ABOUT US</a>
  <a style="left:797px" href="#">SERVICES</a>
  <a style="left:908px" href="#">BLOG</a>
  <a style="left:988px" href="#">SEARCH</a>
</header>
<div class="abs brand-box">
  <div class="brand-name"><span class="mark"></span>Foxtrot Lane</div>
  <div class="brand-tag">Spotless Spaces Since Day One</div>
</div>

<div class="abs section-title main" style="top:150px">
  <span class="rule"></span><span class="diamond"></span>
  <h2>Foxtrot Lane</h2>
  <span class="diamond"></span><span class="rule"></span>
</div>
<p class="abs intro">Foxtrot Lane is a locally owned family business dedicated to providing you with quality cleaning services for a reasonable price.</p>

<div class="abs slider-media" role="img" aria-label="Photo of a smiling vintage-styled housekeeper in pink gloves holding a cleaning cloth and spray bottle"></div>
<p class="abs slider-caption">Foxtrot Lane is a family owned professional cleaning business. We provide our years of cleaning experience to homes and businesses in and around Portland, Oregon.</p>
<div class="abs slider-dots"><i></i><i></i><i class="on"></i></div>
<div class="abs quote-btn">GET A QUOTE TODAY</div>

<section>
  <div class="abs section-title" style="top:1003px">
    <span class="rule"></span><span class="diamond"></span>
    <h2>About Us</h2>
    <span class="diamond"></span><span class="rule"></span>
  </div>
  <h3 class="abs about-heading">Making the Greater Portland Area Clean, One Building at a Time</h3>
  <p class="abs about-text">Foxtrot Lane is a locally owned family business dedicated to providing you with quality cleaning services for a reasonable price. We provide flexible 24 hour service and we are available for cleaning emergencies.</p>
  <div class="btn" style="left:479px;top:1237px;width:119px">Learn More</div>
  <div class="btn" style="left:604px;top:1237px;width:119px">Leave a Review</div>
  <div class="abs about-link">CLEANING AND MAINTENANCE</div>
</section>

<section>
  <div class="abs section-title" style="top:1520px">
    <span class="rule" style="width:160px"></span><span class="diamond"></span>
    <h2>Our Services</h2>
    <span class="diamond"></span><span class="rule" style="width:160px"></span>
  </div>

  <div class="service">
    <h3 style="left:174px;top:1652px">General House Keeping</h3>
    <div class="service-photo" style="left:174px;top:1706px;background:linear-gradient(160deg,#e8e2d6,#c9555a 60%,#3b6fa8)" role="img" aria-label="Photo of a housekeeper with a bucket of cleaning supplies"></div>
    <ul style="left:367px;top:1741px"><li>Floor to ceiling dusting</li><li>Cobweb removal</li><li>Kitchen Cleaning</li><li>Bathroom cleaning</li><li>Sweep, mop and vacuum floors</li></ul>
  </div>
  <div class="service">
    <h3 style="left:645px;top:1652px">Move Outs &amp; Detail</h3>
    <div class="service-photo" style="left:645px;top:1706px;background:linear-gradient(160deg,#d9dee3,#9aa4ad 60%,#6d7f5a)" role="img" aria-label="Photo of a window being washed outside a house"></div>
    <ul style="left:838px;top:1741px"><li>Leaf blowing</li><li>Pressure washing</li><li>Window washing</li><li>Exterior house detail</li><li>Gutter cleaning</li></ul>
  </div>
  <div class="service">
    <h3 style="left:174px;top:1955px">Exterior Services</h3>
    <div class="service-photo" style="left:174px;top:2009px;background:linear-gradient(160deg,#7fb6e0,#3f7fb8 60%,#1f3f66)" role="img" aria-label="Photo of window cleaners on a glass office building"></div>
    <ul style="left:367px;top:2044px"><li>All general house keeping</li><li>Make your house "move in" ready</li><li>Refrigerator and oven cleaning</li><li>Window washing</li><li>Carpet cleaning</li></ul>
  </div>
  <div class="service">
    <h3 style="left:645px;top:1955px">Event Services</h3>
    <div class="service-photo" style="left:645px;top:2009px;background:linear-gradient(160deg,#4a5a78,#2c3440 60%,#c7a070)" role="img" aria-label="Photo of a filming crew at an indoor event"></div>
    <ul style="left:838px;top:2044px"><li>vent hosting at the elm street</li><li class="cont">studio Event cleanup</li></ul>
  </div>
</section>

<section>
  <div class="abs section-title" style="top:2418px">
    <span class="rule"></span><span class="diamond"></span>
    <h2>Latest Blog</h2>
    <span class="diamond"></span><span class="rule"></span>
  </div>
  <h3 class="abs blog-sub">The latest news from Foxtrot Lane</h3>

  <article>
    <div class="post-card" style="left:164px;top:2596px">
      <div class="photo" style="background:linear-gradient(150deg,#6b4a3a,#a33a2e 55%,#2e2e2e)" role="img" aria-label="Photo of a musician playing guitar on stage"></div>
      <span class="cam"></span><div class="label">Foxtrot Lane</div>
    </div>
    <h4 class="post-title" style="left:340px;top:2603px">Foxtrot Lane Returns to Riverside Rhythm Festival 2017</h4>
    <div class="post-meta" style="left:340px;top:2656px">Posted in Events by Marion Hale on July 15, 2017</div>
    <div class="post-date" style="left:340px;top:2697px">31<small>July</small></div>
    <p class="post-excerpt" style="left:384px;top:2697px">Foxtrot Lane returns to the Riverside Rhythm Festival this June 30 through July 4, 2017. Say hi to us as we run a kids</p>
    <a class="post-more" style="left:340px;top:2751px">Learn More</a>
  </article>
  <article>
    <div class="post-card" style="left:615px;top:2596px">
      <div class="photo" style="background:linear-gradient(150deg,#5aa8d8,#d86aa8 55%,#f0c850)" role="img" aria-label="Photo of a child in a colourful festival hat"></div>
      <span class="cam"></span><div class="label">Foxtrot Lane</div>
    </div>
    <h4 class="post-title" style="left:791px;top:2603px">Foxtrot Lane sponsoring Riverside Rhythm Fest 2016</h4>
    <div class="post-meta" style="left:791px;top:2656px">Posted in Events by Marion Hale on May 16,2016</div>
    <div class="post-date" style="left:791px;top:2697px">31<small>July</small></div>
    <p class="post-excerpt" style="left:835px;top:2697px">Foxtrot Lane will be sponsoring the Kids Booth at the Riverside Rhythm Festival in July! www.riversiderhythmfest.com</p>
    <a class="post-more" style="left:791px;top:2751px">Learn More</a>
  </article>

  <div class="btn" style="left:531px;top:2834px;width:133px;height:42px">View More Blogs</div>
</section>

<section>
  <div class="abs section-title dark" style="top:3064px">
    <span class="rule"></span><span class="diamond"></span>
    <h2>Contact Us</h2>
    <span class="diamond"></span><span class="rule"></span>
  </div>
  <p class="abs contact-lead">Contact us for a quote, to book a cleaning, or for any other reason. We're looking forward to hearing from you!</p>

  <div class="field" style="top:3287px;height:43px">Enter Your Name</div>
  <div class="field" style="top:3354px;height:43px">Enter Your Mail</div>
  <div class="field" style="top:3421px;height:43px">Select</div>
  <div class="field" style="top:3491px;height:111px">Message</div>
  <div class="abs submit">Submit</div>

  <div class="info-rule" style="top:3290px"></div>
  <div class="info-row" style="top:3320px">
    <svg viewBox="0 0 22 18"><rect x="1" y="1" width="20" height="16" fill="none" stroke="#fff" stroke-width="2"/><rect x="4" y="5" width="6" height="6" fill="#fff"/></svg>
    <span>ADDRESS&nbsp; // &nbsp;418 SE Alder St #210, Portland, OR 97214</span>
  </div>
  <div class="info-row" style="top:3367px">
    <svg viewBox="0 0 22 18"><path d="M3 5 Q11 -1 19 5 L17 8 L14 6 L8 6 L5 8 Z" fill="#fff"/><rect x="5" y="9" width="12" height="8" fill="#fff"/></svg>
    <span>PHONE&nbsp; // &nbsp;971-555-0148</span>
  </div>
  <div class="info-row" style="top:3407px">
    <svg viewBox="0 0 22 18"><rect x="1" y="2" width="20" height="14" fill="#fff"/><path d="M1 2 L11 10 L21 2" fill="none" stroke="#2b2b2b" stroke-width="2"/></svg>
    <span>E-mail&nbsp; // &nbsp;marion@foxtrotlane.com</span>
  </div>
  <div class="info-rule" style="top:3458px"></div>

  <span class="social" style="left:610px" aria-label="Social link"></span>
  <span class="social" style="left:694px" aria-label="Social link"></span>
  <span class="social" style="left:779px" aria-label="Social link"></span>
  <span class="social" style="left:865px" aria-label="Social link"></span>

  <p class="abs copyright">Copyright ©2018 Foxtrot Lane. All Rights Reserved</p>
</section>

</body>
</html>
```